Quillmarsh Property Solutions need a business card design

Hello guys. We would need a business card design asap please.
We are a start up property investment business based in London UK specialised in buying, selling, managing and letting properties and helping distressed property owners.
The name of our Business is Quillmarsh, the logo symbolises the four fundamental elements of the world (earth, air, fire and water) and so it stands for strength, stability, longevity.
We would like the business card to communicate professionalism and reliability. Many many thanks indeed for your work.

Details:

1.) Rosalind Updike
Property Investor
Mobile: +44(0)7700123456
Email: rosalind.quillmarsh@mailbox-example.com

2.) Dominic Updike
Property Investor
Mobile: +44(0)7700987654
Email: dominic.quillmarsh@mailbox-example.com

```html
<!DOCTYPE html>
<html lang="en">
<head>
<meta charset="utf-8">
<title>Quillmarsh Property Solutions – Business Card</title>
<link rel="stylesheet" href="https://fonts.googleapis.com/css2?family=Josefin+Sans:wght@700&family=Open+Sans:wght@400;600&display=swap">
<style>
  :root {
    --backdrop: #e9e6e1;
    --card: #ffffff;
    --ink: #111111;
    --ink-soft: #555a60;
    --brand-red: #c8283a;
    --brand-blue: #2d4f9e;
    --icon-green: #2e8b4a;
  }
  * { box-sizing: border-box; margin: 0; padding: 0; }
  html, body {
    width: 1200px;
    height: 720px;
    overflow: hidden;
    background: var(--backdrop);
  }
  .canvas {
    width: 1200px;
    height: 720px;
    display: flex;
    align-items: center;
    justify-content: center;
    gap: 40px;
  }
  .card {
    position: relative;
    width: 540px;
    height: 310px;
    background: var(--card);
    box-shadow: 0 2px 10px rgba(0,0,0,0.12);
    overflow: hidden;
  }

  /* Front side */
  .wordmark {
    position: absolute;
    top: 78px;
    left: 0;
    right: 0;
    text-align: center;
    font-family: "Josefin Sans", sans-serif;
    font-weight: 700;
    color: var(--ink);
    text-transform: uppercase;
  }
  .wordmark__name {
    display: block;
    font-size: 30px;
    letter-spacing: 1px;
  }
  .wordmark__tagline {
    display: block;
    margin-top: 4px;
    font-size: 11px;
    letter-spacing: 0.5px;
  }
  .contact-row {
    position: absolute;
    top: 200px;
    left: 0;
    right: 0;
    display: flex;
    justify-content: center;
    align-items: center;
    gap: 8px;
    font-family: "Open Sans", sans-serif;
    font-size: 12.5px;
    color: var(--ink-soft);
  }
  .contact-row__item { display: flex; align-items: center; gap: 5px; }
  .contact-row__divider { color: #9a9ea3; }
  .contact-row svg { width: 12px; height: 12px; fill: var(--icon-green); }
  .rule-blue {
    position: absolute;
    top: 236px;
    left: 0;
    right: 0;
    height: 2px;
    background: var(--brand-blue);
  }
  .name-band {
    position: absolute;
    top: 244px;
    left: 0;
    right: 0;
    height: 38px;
    background: var(--brand-red);
    display: flex;
    align-items: center;
    justify-content: center;
    font-family: "Open Sans", sans-serif;
    color: #ffffff;
    font-size: 14px;
  }
  .name-band__name { font-weight: 600; text-transform: uppercase; letter-spacing: 0.3px; }
  .name-band__role { font-weight: 400; margin-left: 5px; }

  /* Back side */
  .card--back {
    display: flex;
    flex-direction: column;
    align-items: center;
    justify-content: center;
    font-family: "Josefin Sans", sans-serif;
    font-weight: 700;
    color: var(--ink);
    text-transform: uppercase;
  }
  .back-name { font-size: 54px; letter-spacing: 2px; line-height: 1; }
  .back-tagline { font-size: 24px; letter-spacing: 1px; margin-top: 10px; }
</style>
</head>
<body>
<main class="canvas">
  <section class="card card--front" aria-label="Business card front">
    <div class="wordmark">
      <span class="wordmark__name">Quillmarsh</span>
      <span class="wordmark__tagline">Property Solutions</span>
    </div>
    <div class="contact-row">
      <span class="contact-row__item">
        <svg viewBox="0 0 12 12" aria-hidden="true"><rect x="3" y="0.5" width="6" height="11" rx="1.2"/><rect x="4" y="2" width="4" height="6" fill="#fff"/></svg>
        +44(0)7700987654
      </span>
      <span class="contact-row__divider">|</span>
      <span class="contact-row__item">
        <svg viewBox="0 0 12 12" aria-hidden="true"><rect x="0.5" y="2.5" width="11" height="7.5" rx="1"/><path d="M1 3 L6 7 L11 3" stroke="#fff" stroke-width="1" fill="none"/></svg>
        dominic.quillmarsh@mailbox-example.com
      </span>
    </div>
    <div class="rule-blue"></div>
    <div class="name-band">
      <span class="name-band__name">Dominic Updike,</span>
      <span class="name-band__role">Property Investor</span>
    </div>
  </section>

  <section class="card card--back" aria-label="Business card back">
    <span class="back-name">Quillmarsh</span>
    <span class="back-tagline">Property Solutions</span>
  </section>
</main>
</body>
</html>
```